Business Card for Fashion House

We need a business card design for our personalize fashion service for our customers. the business card should reflect reliability, luxury and creativity.
The brand Gravetto is extracted from "Graceful Velvetto"; Gravetto provides fashion designs sprinkled with luxury and style tailored for our elite clients character profile.
Gravetto is created for those who embody class and elegance with a passion for style.
Target Market(s)
Affluent Customers
Industry/Entity Type
Fashion
Contact Information for Business Card
Samira Haddadin
Fashion Designer
Telephone: +971 4 555 0192
Mobile +971 50 555 0147
Emal info@gravetto-example.com
Website www.gravetto-example.com
Social Media Youtube g+ Facebook Instagram Pin /gravetto
Font styles to use
Other font styles liked:
- Audrey provided
Look and feel
Each slider illustrates characteristics of the customer's brand and the style your logo design should communicate.

```html
<!DOCTYPE html>
<html lang="en">
<head>
<meta charset="utf-8">
<title>Gravetto Business Card</title>
<link href="https://fonts.googleapis.com/css2?family=Marcellus&family=Lato:wght@400;700&display=swap" rel="stylesheet">
<style>
  :root {
    --canvas: #e9e7e5;
    --card-white: #f6f6f5;
    --card-dark: #3a3432;
    --ink: #2b2b2b;
    --ink-soft: #555;
    --swoosh-light: #d9d9d9;
    --swoosh-mid: #8a8a8a;
    --rule: #6b6b6b;
    --on-dark: #f2f2f2;
    --on-dark-soft: #6f6866;
  }
  html, body {
    margin: 0;
    width: 1200px;
    height: 1000px;
    overflow: hidden;
    background: var(--canvas);
  }
  .canvas {
    position: relative;
    width: 1200px;
    height: 1000px;
  }
  .card {
    position: absolute;
    left: 250px;
    width: 700px;
    height: 400px;
    border-radius: 22px;
    overflow: hidden;
    box-shadow: 0 10px 28px rgba(0,0,0,.18);
  }
  .card-front { top: 70px; background: var(--card-white); }
  .card-back  { top: 530px; background: var(--card-dark); }

  .front-swoosh { position: absolute; inset: 0; }

  .front-brand {
    position: absolute;
    left: 40px;
    top: 110px;
    width: 270px;
    display: flex;
    flex-direction: column;
    align-items: center;
    gap: 26px;
  }
  .brand-dot {
    width: 58px;
    height: 58px;
    border-radius: 50%;
    border: 2px solid var(--ink);
    box-sizing: border-box;
  }
  .brand-name {
    font-family: "Marcellus", serif;
    font-weight: 400;
    text-transform: uppercase;
    letter-spacing: .32em;
    color: var(--ink);
    font-size: 30px;
    margin: 0;
  }
  .divider {
    position: absolute;
    left: 330px;
    top: 55px;
    width: 1.5px;
    height: 210px;
    background: var(--rule);
  }
  .contact {
    position: absolute;
    left: 352px;
    top: 48px;
    font-family: "Lato", sans-serif;
    color: var(--ink);
  }
  .contact-name {
    font-family: "Marcellus", serif;
    font-size: 22px;
    text-transform: uppercase;
    margin: 0;
    letter-spacing: .02em;
  }
  .contact-role {
    font-family: "Marcellus", serif;
    font-size: 14px;
    margin: 2px 0 12px;
    color: var(--ink-soft);
  }
  .contact-list { list-style: none; margin: 0; padding: 0; }
  .contact-list li {
    display: flex;
    align-items: center;
    gap: 9px;
    font-size: 14px;
    line-height: 24px;
  }
  .contact-list svg { width: 14px; height: 14px; flex: none; }
  .social {
    display: flex;
    align-items: center;
    gap: 9px;
    margin-top: 18px;
    font-size: 14px;
  }
  .social-dot {
    width: 18px;
    height: 18px;
    border-radius: 50%;
    background: var(--ink);
  }

  .back-brand {
    position: absolute;
    inset: 0;
    display: flex;
    flex-direction: column;
    align-items: center;
    justify-content: center;
    gap: 22px;
  }
  .back-brand .brand-dot { width: 80px; height: 80px; border: 3px solid var(--on-dark); }
  .back-brand .brand-name { color: var(--on-dark); font-size: 48px; letter-spacing: .3em; margin-left: .3em; }
  .back-web {
    font-family: "Lato", sans-serif;
    font-size: 17px;
    color: var(--on-dark-soft);
    margin: 0;
  }
  .back-web strong { font-weight: 700; }
</style>
</head>
<body>
<div class="canvas">

  <section class="card card-front">
    <svg class="front-swoosh" viewBox="0 0 700 400" preserveAspectRatio="none" aria-hidden="true">
      <path d="M0 400 L0 370 C120 360 260 300 420 250 C540 212 640 215 700 225 L700 400 Z" fill="var(--swoosh-mid)"/>
      <path d="M0 400 L0 385 C140 375 280 318 430 268 C550 230 640 232 700 240 L700 400 Z" fill="var(--swoosh-light)"/>
      <path d="M0 400 C160 395 300 335 440 288 C560 250 640 250 700 255 L700 400 Z" fill="var(--card-white)"/>
    </svg>

    <div class="front-brand">
      <span class="brand-dot"></span>
      <p class="brand-name">Gravetto</p>
    </div>

    <div class="divider"></div>

    <div class="contact">
      <h1 class="contact-name">Samira Haddadin</h1>
      <p class="contact-role">Fashion Designer</p>
      <ul class="contact-list">
        <li>
          <svg viewBox="0 0 16 16"><rect x="1" y="6" width="14" height="9" rx="2" fill="var(--ink)"/><path d="M2 6 C2 1 14 1 14 6" stroke="var(--ink)" stroke-width="2" fill="none"/></svg>
          +971 4 555 0192
        </li>
        <li>
          <svg viewBox="0 0 16 16"><path d="M3 1 L6 1 L7 5 L5 6.5 C6 9 7 10 9.5 11 L11 9 L15 10 L15 13 C15 14 14 15 13 15 C6 15 1 10 1 3 C1 2 2 1 3 1 Z" fill="var(--ink)"/></svg>
          +971 50 555 0147
        </li>
        <li>
          <svg viewBox="0 0 16 16"><circle cx="8" cy="8" r="7" fill="var(--ink)"/><path d="M1 8 H15 M8 1 C4 5 4 11 8 15 M8 1 C12 5 12 11 8 15" stroke="var(--card-white)" stroke-width="1" fill="none"/></svg>
          www.gravetto-example.com
        </li>
        <li>
          <svg viewBox="0 0 16 16"><circle cx="8" cy="8" r="7" fill="var(--ink)"/><rect x="4" y="5" width="8" height="6" fill="none" stroke="var(--card-white)" stroke-width="1"/><path d="M4 5 L8 8.5 L12 5" stroke="var(--card-white)" stroke-width="1" fill="none"/></svg>
          info@gravetto-example.com
        </li>
      </ul>
      <div class="social">
        <span class="social-dot"></span>
        <span class="social-dot"></span>
        <span class="social-dot"></span>
        <span class="social-dot"></span>
        <span class="social-dot"></span>
        <span>/gravetto</span>
      </div>
    </div>
  </section>

  <section class="card card-back">
    <div class="back-brand">
      <span class="brand-dot"></span>
      <p class="brand-name">Gravetto</p>
      <p class="back-web">www.<strong>gravetto-example</strong>.com</p>
    </div>
  </section>

</div>
</body>
</html>
```